Medical Transport Vehicle Wrap

We need a wrap to cover multiple passenger van involved in non-emergent medical transport services in Alaska. The organization is involved in Mobile Integrated Healthcare and the vans go to the patient's home and visit the client and make sure they are doing well. The vans are fully equipped with advanced level of care, paramedics, and EMTs. They will sometimes transport people from home to an appointment or to other locations, but it will be mostly a van to move the medical team around. Our colors are red and blue and we want to use the vans as mobile billboards. The goal is mostly to get new clients with this wrap.

We do not want it to cover the windows or be on the front of the van. We want the wrap to be simple and reduce the amount of material as much as possible. We want the wrap to be professional, clean, but eye catching.

See attached logo. Our website is www.terovantis.com, but this project is not listed on the website. So be aware.

These will be going on a 2019 brelco wayfarer.
Updates

These designs are not what I am looking for. I would like something more elegant and proffesional

Colors
0054AA
0677BA
7BADD7
CADEEF
E8F1F8
EB3D1F
EC4F4E
F09395
F8D3D4
FCEDEE

Requirements
Must have
• Logo, phone number, website

```html
<!DOCTYPE html>
<html lang="en">
<head>
<meta charset="utf-8">
<title>Vantis Medical – Van Wrap Concepts</title>
<link rel="stylesheet" href="https://fonts.googleapis.com/css2?family=Montserrat:wght@600;700;800&family=Open+Sans:wght@500;600&display=swap">
<style>
  :root {
    --navy: #10128c;
    --red: #c0141f;
    --white: #ffffff;
    --body: #f4f4f5;
    --body-edge: #d9d9dc;
    --frame: #4a4a4d;
    --glass: #a9a9ad;
    --tyre: #1d1d1f;
    --rim: #5c5c60;
    --hub: #2a2a2d;
    --tail: #d3262e;
    --shadow: rgba(0,0,0,0.18);
  }
  html, body {
    margin: 0;
    padding: 0;
    width: 1200px;
    height: 1200px;
    overflow: hidden;
    background: var(--white);
  }
  .canvas { display: block; width: 1200px; height: 1200px; }
  .van-body { fill: var(--body); stroke: var(--body-edge); stroke-width: 3; }
  .window-frame { fill: var(--frame); }
  .window-glass { fill: var(--glass); }
  .tail-light { fill: var(--tail); }
  .head-light { fill: #e6e6e8; stroke: #9a9a9e; stroke-width: 3; }
  .ground-shadow { fill: var(--shadow); }
  .tyre { fill: var(--tyre); }
  .rim { fill: var(--rim); }
  .hub { fill: var(--hub); }
  .wrap-navy { fill: var(--navy); }
  .wrap-red { fill: var(--red); }
  .wrap-white-line { fill: none; stroke: var(--white); stroke-width: 6; }
  .brand-mark { fill: var(--red); }
  .brand-name {
    font-family: "Montserrat", sans-serif;
    font-weight: 800;
    fill: var(--navy);
  }
  .contact-label {
    font-family: "Montserrat", sans-serif;
    font-weight: 700;
    font-size: 34px;
    letter-spacing: 1px;
  }
  .contact-phone {
    font-family: "Montserrat", sans-serif;
    font-weight: 700;
  }
  .web-address {
    font-family: "Open Sans", sans-serif;
    font-weight: 600;
    font-size: 34px;
    letter-spacing: 2px;
    fill: var(--white);
  }
  .on-navy { fill: var(--white); }
  .label-red { fill: var(--red); }
  .phone-navy { fill: var(--navy); }
</style>
</head>
<body>
<svg class="canvas" viewBox="0 0 1920 1920" xmlns="http://www.w3.org/2000/svg">
  <defs>
    <path id="van-shell" d="M110,800 L108,680 L140,590 L200,555 L480,500 L760,330 L960,300 L1700,300 L1715,330 L1790,490 L1845,630 L1852,700 L1848,765 L1650,800 L1360,815 L600,825 L160,820 Z"/>
    <path id="van-windows" d="M495,528 L760,335 L1700,318 L1705,470 L1370,490 Z"/>
  </defs>

  <!-- Concept A: diagonal rear panel -->
  <g class="van concept-diagonal">
    <ellipse class="ground-shadow" cx="980" cy="880" rx="850" ry="22"/>
    <use href="#van-shell" class="van-body"/>
    <g role="img" aria-label="Navy rear panel with faint mountain range texture">
      <polygon class="wrap-navy" points="1075,296 1700,298 1790,490 1848,640 1850,760 1650,800 1355,812 1190,490 1075,490"/>
    </g>
    <use href="#van-windows" class="window-frame"/>
    <polygon class="window-glass" points="635,505 760,385 925,378 925,500"/>
    <rect class="window-glass" x="985" y="368" width="265" height="128"/>
    <rect class="window-glass" x="1390" y="372" width="145" height="78"/>
    <path class="tail-light" d="M1740,500 L1800,500 L1818,560 L1818,620 L1762,600 Z"/>
    <path class="head-light" d="M140,590 L232,573 L200,640 L148,640 Z"/>

    <polygon class="wrap-red" points="605,760 1322,754 1345,796 612,800"/>
    <text class="web-address" x="950" y="791" text-anchor="middle">www.terovantis.com</text>

    <circle class="brand-mark" cx="752" cy="637" r="95"/>
    <text class="brand-name" x="862" y="662" font-size="100">VANTIS</text>
    <text class="brand-name" x="1018" y="716" font-size="46" text-anchor="middle" letter-spacing="4">Medical</text>

    <text class="contact-label on-navy" x="1478" y="545" text-anchor="middle">Contact Us:</text>
    <text class="contact-phone on-navy" x="1478" y="601" font-size="46" text-anchor="middle">1-907-555-0148</text>

    <g class="wheel">
      <circle class="tyre" cx="398" cy="785" r="130"/>
      <circle class="rim" cx="398" cy="785" r="88"/>
      <circle class="hub" cx="398" cy="785" r="20"/>
    </g>
    <g class="wheel">
      <circle class="tyre" cx="1505" cy="785" r="130"/>
      <circle class="rim" cx="1505" cy="785" r="88"/>
      <circle class="hub" cx="1505" cy="785" r="20"/>
    </g>
  </g>

  <!-- Concept B: lower wave band -->
  <g class="van concept-wave" transform="translate(0,740)">
    <ellipse class="ground-shadow" cx="980" cy="880" rx="850" ry="22"/>
    <use href="#van-shell" class="van-body"/>
    <path class="wrap-navy" d="M540,725 Q800,760 1000,752 Q1250,738 1400,680 Q1620,640 1850,690 L1848,765 L1650,800 L1360,815 L600,825 L545,822 Z"/>
    <path class="wrap-white-line" d="M540,716 Q800,751 1000,743 Q1250,729 1400,671 Q1620,631 1850,681"/>
    <path class="wrap-red" d="M540,712 Q800,742 1000,732 Q1250,716 1400,656 Q1620,616 1850,668 L1850,676 Q1620,626 1400,666 Q1250,726 1000,740 Q800,748 540,720 Z"/>
    <use href="#van-windows" class="window-frame"/>
    <polygon class="window-glass" points="635,505 760,385 925,378 925,500"/>
    <rect class="window-glass" x="985" y="368" width="265" height="128"/>
    <rect class="window-glass" x="1390" y="372" width="145" height="78"/>
    <path class="tail-light" d="M1740,500 L1800,500 L1818,560 L1818,620 L1762,600 Z"/>
    <path class="head-light" d="M140,590 L232,573 L200,640 L148,640 Z"/>

    <circle class="brand-mark" cx="762" cy="632" r="85"/>
    <text class="brand-name" x="865" y="652" font-size="94">VANTIS</text>
    <text class="brand-name" x="1005" y="702" font-size="44" text-anchor="middle" letter-spacing="4">Medical</text>

    <text class="contact-label label-red" x="1485" y="542" text-anchor="middle">Contact Us:</text>
    <text class="contact-phone phone-navy" x="1485" y="606" font-size="52" text-anchor="middle">1-907-555-0148</text>

    <text class="web-address" x="985" y="800" text-anchor="middle">www.terovantis.com</text>

    <g class="wheel">
      <circle class="tyre" cx="398" cy="785" r="130"/>
      <circle class="rim" cx="398" cy="785" r="88"/>
      <circle class="hub" cx="398" cy="785" r="20"/>
    </g>
    <g class="wheel">
      <circle class="tyre" cx="1505" cy="785" r="130"/>
      <circle class="rim" cx="1505" cy="785" r="88"/>
      <circle class="hub" cx="1505" cy="785" r="20"/>
    </g>
  </g>
</svg>
</body>
</html>
```